Print on top the name of the company: (Or Similar)
Lumora Cleaning & Disinfecting
Because your standards aren't standard.

We adhere to ALL QRV guidelines for both residential and commercial cleaning.

Infection Control is our ultimate goal.

Instructions:
Opening a residential and commercial cleaning and disinfecting company in south Florida.

Targeting high-end residential clients, commercial and healthcare facilities, specializing in Ambulatory Care Guidelines. With a concentration and expertise in targeting Covid 19 and other transmissible pathogens.

WELM trained.
Owned and operated by a licensed BSN Registered Nurse specially ​trained in Infection Control Prevention with over 25 years experience. Over two decades in Ambulatory Surgery Center Administration, Director of Nursing and Infection Control Prevention ad Consulting.

Looking to create a business flier that emphasizes Cleaning & Disinfection
along with the standard expectation for residential and Commercial cleaning services

Target Market(s)

Residential & Commercial

Font styles to use
Decorative

Requirements
Must have
• A checklist for cleaning services

```html
<!DOCTYPE html>
<html lang="en">
<head>
<meta charset="utf-8">
<title>Lumora Cleaning &amp; Disinfecting – Flyer</title>
<link rel="stylesheet" href="https://fonts.googleapis.com/css2?family=Montserrat:wght@600;700;800&family=Satisfy&display=block">
<style>
  :root {
    --yellow: #fcd80a;
    --yellow-deep: #f7c20a;
    --pill-yellow: #f0d63c;
    --green: #9dba3b;
    --panel-grey: #ebebeb;
    --bg-grey: #e9e9e9;
    --ink: #262626;
    --white: #ffffff;
    --tick: #7cc24a;
  }
  * { box-sizing: border-box; margin: 0; padding: 0; }
  html, body { width: 1200px; height: 1200px; overflow: hidden; background: var(--white); }
  body { position: relative; font-family: "Montserrat", Arial, sans-serif; color: var(--ink); }

  .flyer {
    position: absolute; left: 112px; top: 256px; width: 981px; height: 694px;
    background: radial-gradient(ellipse at 50% 55%, #f8f8f8 0%, var(--bg-grey) 70%);
    overflow: hidden;
    box-shadow: 0 2px 10px rgba(0,0,0,.12);
  }
  .header-band { position: absolute; left: 0; top: 0; width: 100%; height: 160px; }
  .brand-title {
    position: absolute; left: 0; top: 26px; width: 100%; height: 80px; text-align: center;
    white-space: nowrap; overflow: visible;
    font-family: "Satisfy", "Brush Script MT", cursive; font-weight: 400;
    font-size: 64px; line-height: 80px; color: var(--ink); letter-spacing: 1px;
  }

  .service-card {
    position: absolute; top: 181px; height: 316px;
    background: var(--panel-grey); border-radius: 20px; overflow: hidden;
  }
  .service-card--commercial { left: 64px; width: 422px; }
  .service-card--residential { left: 511px; width: 418px; }
  .service-card__title {
    height: 64px; background: var(--green); color: var(--white);
    font-weight: 700; font-size: 40px; letter-spacing: 2px; text-align: center; line-height: 66px;
  }
  .service-list {
    position: absolute; top: 80px; list-style: none;
    font-weight: 600; font-size: 13.5px; line-height: 22px;
  }
  .service-list li { display: flex; align-items: flex-start; gap: 6px; }
  .service-list svg { flex: none; margin-top: 6px; }
  .service-card--commercial .service-list--a { left: 39px; }
  .service-card--commercial .service-list--b { left: 217px; }
  .service-card--residential .service-list--a { left: 34px; }
  .service-card--residential .service-list--b { left: 236px; width: 160px; }
  .service-list .wrap { line-height: 17px; padding-top: 3px; }

  .service-card__photo { position: absolute; left: 0; bottom: 0; width: 100%; height: 122px; }
  .photo-commercial { background: linear-gradient(90deg, #3a3b3d 0%, #8c8d8f 30%, #dcdcdc 50%, #a9aaab 75%, #3d3e40 100%); }
  .photo-residential { background: linear-gradient(180deg, #ece9e4 0%, #d9d3ca 55%, #cfcac4 100%); }

  .footer-band { position: absolute; left: 0; bottom: 0; width: 100%; height: 125px; }
  .offer-pill {
    position: absolute; left: 53px; top: 539px; width: 876px; height: 56px;
    background: var(--pill-yellow); border-radius: 28px;
    font-weight: 700; font-size: 25px; text-align: center; line-height: 56px;
  }
  .phone-line {
    position: absolute; left: 0; top: 600px; width: 100%;
    display: flex; justify-content: center; align-items: center; gap: 22px;
    font-weight: 700; font-size: 80px; line-height: 1; letter-spacing: 1px;
  }
</style>
</head>
<body>
<div class="flyer">
  <svg class="header-band" viewBox="0 0 981 160" preserveAspectRatio="none" aria-hidden="true">
    <defs>
      <radialGradient id="sun" cx="50%" cy="100%" r="80%">
        <stop offset="0" stop-color="#fde714"/>
        <stop offset="1" stop-color="#f9c90a"/>
      </radialGradient>
    </defs>
    <path d="M0 0H981V118Q490 166 0 118Z" fill="url(#sun)"/>
    <path d="M0 124Q490 168 981 124V135Q490 162 0 135Z" fill="#9dba3b"/>
    <path d="M0 118Q490 166 981 118V124Q490 168 0 124Z" fill="#ffffff"/>
  </svg>
  <h1 class="brand-title">Lumora Cleaning &amp; Disinfecting</h1>

  <section class="service-card service-card--commercial">
    <h2 class="service-card__title">COMMERCIAL</h2>
    <ul class="service-list service-list--a">
      <li><svg width="10" height="10" viewBox="0 0 10 10"><circle cx="5" cy="5" r="5" fill="#7cc24a"/><path d="M2.6 5.2l1.6 1.5 3.2-3.3" stroke="#fff" stroke-width="1.4" fill="none"/></svg>Janitorial</li>
      <li><svg width="10" height="10" viewBox="0 0 10 10"><circle cx="5" cy="5" r="5" fill="#7cc24a"/><path d="M2.6 5.2l1.6 1.5 3.2-3.3" stroke="#fff" stroke-width="1.4" fill="none"/></svg>Offices</li>
      <li><svg width="10" height="10" viewBox="0 0 10 10"><circle cx="5" cy="5" r="5" fill="#7cc24a"/><path d="M2.6 5.2l1.6 1.5 3.2-3.3" stroke="#fff" stroke-width="1.4" fill="none"/></svg>Floor maintenance</li>
      <li><svg width="10" height="10" viewBox="0 0 10 10"><circle cx="5" cy="5" r="5" fill="#7cc24a"/><path d="M2.6 5.2l1.6 1.5 3.2-3.3" stroke="#fff" stroke-width="1.4" fill="none"/></svg>Carpet cleaning</li>
    </ul>
    <ul class="service-list service-list--b">
      <li><svg width="10" height="10" viewBox="0 0 10 10"><circle cx="5" cy="5" r="5" fill="#7cc24a"/><path d="M2.6 5.2l1.6 1.5 3.2-3.3" stroke="#fff" stroke-width="1.4" fill="none"/></svg>Move-ins</li>
      <li><svg width="10" height="10" viewBox="0 0 10 10"><circle cx="5" cy="5" r="5" fill="#7cc24a"/><path d="M2.6 5.2l1.6 1.5 3.2-3.3" stroke="#fff" stroke-width="1.4" fill="none"/></svg>Move-outs.</li>
      <li><svg width="10" height="10" viewBox="0 0 10 10"><circle cx="5" cy="5" r="5" fill="#7cc24a"/><path d="M2.6 5.2l1.6 1.5 3.2-3.3" stroke="#fff" stroke-width="1.4" fill="none"/></svg>Constructions clean-ups</li>
      <li><svg width="10" height="10" viewBox="0 0 10 10"><circle cx="5" cy="5" r="5" fill="#7cc24a"/><path d="M2.6 5.2l1.6 1.5 3.2-3.3" stroke="#fff" stroke-width="1.4" fill="none"/></svg>Estate clean-outs</li>
    </ul>
    <div class="service-card__photo photo-commercial" role="img" aria-label="Photo: technician in protective suit spraying disinfectant in a modern office"></div>
  </section>

  <section class="service-card service-card--residential">
    <h2 class="service-card__title">RESIDENTIAL</h2>
    <ul class="service-list service-list--a">
      <li><svg width="10" height="10" viewBox="0 0 10 10"><circle cx="5" cy="5" r="5" fill="#7cc24a"/><path d="M2.6 5.2l1.6 1.5 3.2-3.3" stroke="#fff" stroke-width="1.4" fill="none"/></svg>House cleaning</li>
      <li><svg width="10" height="10" viewBox="0 0 10 10"><circle cx="5" cy="5" r="5" fill="#7cc24a"/><path d="M2.6 5.2l1.6 1.5 3.2-3.3" stroke="#fff" stroke-width="1.4" fill="none"/></svg>Before and after party</li>
      <li><svg width="10" height="10" viewBox="0 0 10 10"><circle cx="5" cy="5" r="5" fill="#7cc24a"/><path d="M2.6 5.2l1.6 1.5 3.2-3.3" stroke="#fff" stroke-width="1.4" fill="none"/></svg>Move-ins</li>
      <li><svg width="10" height="10" viewBox="0 0 10 10"><circle cx="5" cy="5" r="5" fill="#7cc24a"/><path d="M2.6 5.2l1.6 1.5 3.2-3.3" stroke="#fff" stroke-width="1.4" fill="none"/></svg>Move-outs</li>
    </ul>
    <ul class="service-list service-list--b">
      <li><svg width="10" height="10" viewBox="0 0 10 10"><circle cx="5" cy="5" r="5" fill="#7cc24a"/><path d="M2.6 5.2l1.6 1.5 3.2-3.3" stroke="#fff" stroke-width="1.4" fill="none"/></svg>Holiday cleaning</li>
      <li><svg width="10" height="10" viewBox="0 0 10 10"><circle cx="5" cy="5" r="5" fill="#7cc24a"/><path d="M2.6 5.2l1.6 1.5 3.2-3.3" stroke="#fff" stroke-width="1.4" fill="none"/></svg>Seasonal cleaning</li>
      <li><svg width="10" height="10" viewBox="0 0 10 10"><circle cx="5" cy="5" r="5" fill="#7cc24a"/><path d="M2.6 5.2l1.6 1.5 3.2-3.3" stroke="#fff" stroke-width="1.4" fill="none"/></svg>Carpet cleaning</li>
      <li><svg width="10" height="10" viewBox="0 0 10 10"><circle cx="5" cy="5" r="5" fill="#7cc24a"/><path d="M2.6 5.2l1.6 1.5 3.2-3.3" stroke="#fff" stroke-width="1.4" fill="none"/></svg><span class="wrap">Deodorizing and sanitizing</span></li>
    </ul>
    <div class="service-card__photo photo-residential" role="img" aria-label="Photo: person vacuuming a light wooden floor in a bright living room"></div>
  </section>

  <svg class="footer-band" viewBox="0 0 981 125" preserveAspectRatio="none" aria-hidden="true">
    <path d="M0 5Q490 -25 981 5V125H0Z" fill="#9dba3b"/>
  </svg>
  <p class="offer-pill">Call us to find out how you can save money this month!</p>
  <p class="phone-line">
    <svg width="68" height="68" viewBox="0 0 24 24" aria-hidden="true"><path fill="#262626" d="M6.6 10.8c1.4 2.8 3.8 5.1 6.6 6.6l2.2-2.2c.3-.3.7-.4 1-.2 1.1.4 2.3.6 3.6.6.6 0 1 .4 1 1V20c0 .6-.4 1-1 1C10.6 21 3 13.4 3 4c0-.6.4-1 1-1h3.5c.6 0 1 .4 1 1 0 1.3.2 2.5.6 3.6.1.3 0 .7-.2 1z"/></svg>
    <span>(305) 555 01 42</span>
  </p>
</div>
</body>
</html>
```